I would like a single page website for Skyward Rentals Pacific. In the file list provided there is basic information to be included as well as our logo with colors, fonts and images to be included.
Site must be very simple and be able to be loaded onto smart phones etc very quickly.
Site needs to be very smart in appearance

Target Market(s)

All prospective drone customers from Police to Parties.

Industry/Entity Type

Hire

Requirements
Must have
• Must have variation of color schemes supplied
Nice to have
• Must be very eye catching without going over the top
Should not have
• Anything slow to load.

```html
<!DOCTYPE html>
<html lang="en">
<head>
<meta charset="utf-8">
<title>Skyward Rentals Pacific</title>
<link href="https://fonts.googleapis.com/css2?family=Roboto+Condensed:wght@400;500;700&family=Arimo:wght@400;700&display=swap" rel="stylesheet">
<style>
:root{
  --green:#86aa2e;
  --green-dark:#739a1e;
  --lime:#8bc21c;
  --lime-text:#9ccb1a;
  --ink:#333333;
  --grey:#666666;
  --rule:#e6e6e6;
  --white:#ffffff;
  --frame:#6e6e6e;
}
*{margin:0;padding:0;box-sizing:border-box}
html,body{width:1022px;height:1200px;overflow:hidden}
body{position:relative;background:var(--white);font-family:"Arimo",Arial,sans-serif;color:var(--ink)}
.top-rule{position:absolute;left:0;top:0;width:100%;height:4px;background:var(--frame)}
.bottom-rule{position:absolute;left:0;bottom:0;width:100%;height:5px;background:var(--frame)}
.paper{position:absolute;left:0;top:120px;width:100%;height:62px;background:#f6f6f6}
.field{position:absolute;left:0;top:180px;width:100%;height:951px;background:var(--green)}
.field-edge{position:absolute;left:0;top:174px;width:100%;height:8px}

.brand{position:absolute;left:84px;top:30px;display:flex;align-items:center;gap:8px}
.brand-dot{width:26px;height:26px;border-radius:50%;background:var(--lime-text)}
.brand-name{font-family:"Roboto Condensed",Arial,sans-serif;font-weight:700;font-size:21px;line-height:22px;color:var(--lime-text);text-transform:uppercase;letter-spacing:1px}

.nav{position:absolute;right:84px;top:58px;display:flex;align-items:center;font-family:"Roboto Condensed",Arial,sans-serif;font-size:12px;font-weight:500}
.nav a{color:var(--ink);text-decoration:none;padding:0 19px;border-left:1px dotted #bbb;line-height:18px}
.nav a:first-child{border-left:none;color:var(--lime-text)}
.nav a:last-child{padding-right:0}

.hero{position:absolute;left:84px;top:122px;width:854px;height:370px;overflow:hidden}
.hero-photo{position:absolute;inset:0;background:linear-gradient(100deg,#b1642b 0%,#d0a27a 25%,#c9bfb9 45%,#9c8fb3 62%,#c987b7 82%,#dca4c7 100%)}
.hero-tint{position:absolute;inset:0;background:linear-gradient(180deg,rgba(62,84,150,.55) 0%,rgba(0,0,0,0) 45%)}
.hero-object{position:absolute;left:60px;top:55px;width:480px;height:270px;border-radius:40px 40px 70px 70px;background:radial-gradient(ellipse at 50% 40%,rgba(245,245,245,.9),rgba(200,200,200,.55) 60%,rgba(200,200,200,0) 72%)}
.hero-copy{position:absolute;left:482px;top:140px}
.hero-title{font-family:"Roboto Condensed",Arial,sans-serif;font-weight:700;font-size:25px;color:#a9c91a;text-transform:uppercase;letter-spacing:.3px}
.hero-sub{margin-top:6px;font-size:12px;color:var(--white)}
.hero-btn{display:inline-block;margin-top:18px;margin-left:-3px;padding:0 16px;height:31px;line-height:31px;background:var(--lime);color:var(--white);font-size:11px;text-transform:uppercase}
.hero-arrows{position:absolute;right:46px;top:308px;display:flex;gap:5px}
.hero-arrows span{width:24px;height:24px;background:rgba(150,150,150,.6);display:flex;align-items:center;justify-content:center}
.hero-shadow{position:absolute;left:120px;top:490px;width:780px;height:22px;border-radius:50%;background:radial-gradient(ellipse at 50% 0%,rgba(0,0,0,.55),rgba(0,0,0,0) 70%)}

.divider{position:absolute;left:84px;top:529px;width:854px;height:2px;background:rgba(255,255,255,.18)}
.pager{position:absolute;left:452px;top:528px;display:flex;gap:6px}
.pager span{width:25px;height:3px;background:var(--white)}
.pager span:first-child{background:#6b6b6b}

.services{position:absolute;left:84px;top:567px;display:flex;gap:13px}
.card{position:relative;width:203px;height:244px;background:var(--white);text-align:center}
.card-img{height:136px}
.card h3{margin-top:16px;font-family:"Roboto Condensed",Arial,sans-serif;font-weight:500;font-size:14px;color:var(--lime-text);text-transform:uppercase;letter-spacing:.3px}
.card p{margin:9px 20px 0;font-size:9px;line-height:16px;color:var(--grey)}
.card .more{margin-top:8px;display:flex;justify-content:center;align-items:center;gap:6px;font-family:"Roboto Condensed",Arial,sans-serif;font-size:9px;color:var(--grey)}
.card::after{content:"";position:absolute;left:8px;right:8px;bottom:-16px;height:16px;border-radius:50%;background:radial-gradient(ellipse at 50% 0%,rgba(0,0,0,.5),rgba(0,0,0,0) 70%)}
.img-wedding{background:linear-gradient(135deg,#9a8a63,#c9b8a4 50%,#efe9e0)}
.img-sport{background:linear-gradient(135deg,#f1b441,#fbe9c4 45%,#c99a7a)}
.img-estate{background:linear-gradient(135deg,#d9dde0,#f1f1f0 50%,#88a7c4)}
.img-camera{background:linear-gradient(135deg,#eef2f8,#c3cde0 60%,#3b3f47)}

.footer-line{position:absolute;left:84px;top:851px;width:854px;height:1px;background:rgba(255,255,255,.14)}
.col{position:absolute;top:880px;color:var(--white)}
.col h2{font-family:"Roboto Condensed",Arial,sans-serif;font-weight:500;font-size:21px;letter-spacing:.3px;text-transform:uppercase}
.about{left:86px;width:270px}
.about p{margin-top:19px;font-size:9px;line-height:17.5px}
.about p + p{margin-top:15px}
.other{left:408px}
.other ul{margin-top:19px;list-style:none}
.other li{font-size:9px;line-height:17.5px;padding-left:16px;position:relative}
.other li::before{content:"";position:absolute;left:2px;top:6px;border-left:4px solid rgba(255,255,255,.45);border-top:3px solid transparent;border-bottom:3px solid transparent}
.location{left:750px;width:190px}
.loc-row{display:flex;align-items:center;gap:8px;margin-top:17px;font-size:9px}
.loc-row + .loc-row{margin-top:7px}
.loc-phone{font-family:"Roboto Condensed",Arial,sans-serif;font-weight:700;font-size:13px}
.follow{margin-top:30px}
.socials{margin-top:17px;display:flex;gap:5px}
.socials span{width:18px;height:18px}

.footbar{position:absolute;left:0;top:1131px;width:100%;height:64px;background:var(--white)}
.copy{position:absolute;left:87px;top:1157px;font-size:10px;color:var(--ink)}
.privacy{position:absolute;right:85px;top:1156px;font-size:10px;color:var(--ink)}
</style>
</head>
<body>
<div class="top-rule"></div>
<div class="paper"></div>
<div class="field"></div>
<svg class="field-edge" viewBox="0 0 1022 8" preserveAspectRatio="none" aria-hidden="true">
  <path d="M0 8 L0 4 Q3 0 6 4 Q9 0 12 4 Q15 0 18 4 L1022 4 L1022 8 Z" fill="#86aa2e"/>
</svg>

<header>
  <div class="brand">
    <span class="brand-dot"></span>
    <span class="brand-name">Skyward Rentals<br>Pacific</span>
  </div>
  <nav class="nav">
    <a href="#">Home</a><a href="#">About Us</a><a href="#">Services</a><a href="#">Our Gallery</a><a href="#">Blog</a><a href="#">Contact Us</a>
  </nav>
</header>

<section class="hero">
  <div class="hero-photo" role="img" aria-label="White camera drone with four rotors on a blurred warm-to-pink backdrop"></div>
  <div class="hero-tint"></div>
  <div class="hero-object"></div>
  <div class="hero-copy">
    <div class="hero-title">Skyward Rentals Pacific</div>
    <div class="hero-sub">We give drones on hire for parties, surveillance, security etc..</div>
    <span class="hero-btn">Read More</span>
  </div>
  <div class="hero-arrows">
    <span><svg width="8" height="12" viewBox="0 0 8 12"><path d="M6 1 L1 6 L6 11" stroke="#fff" stroke-width="1.5" fill="none"/></svg></span>
    <span><svg width="8" height="12" viewBox="0 0 8 12"><path d="M2 1 L7 6 L2 11" stroke="#fff" stroke-width="1.5" fill="none"/></svg></span>
  </div>
</section>
<div class="hero-shadow"></div>

<div class="divider"></div>
<div class="pager"><span></span><span></span><span></span><span></span></div>

<section class="services">
  <article class="card">
    <div class="card-img img-wedding" role="img" aria-label="Bride holding a white bouquet outdoors"></div>
    <h3>Weddings</h3>
    <p>Lorem ipsum dolor sit amet, consectetuer adipiscing elit. Aenean commodo ligula</p>
    <div class="more"><svg width="18" height="8" viewBox="0 0 18 8"><path d="M1 5 Q5 0 9 4 Q13 8 17 2" stroke="#777" fill="none"/></svg>MORE<svg width="18" height="8" viewBox="0 0 18 8"><path d="M1 5 Q5 0 9 4 Q13 8 17 2" stroke="#777" fill="none"/></svg></div>
  </article>
  <article class="card">
    <div class="card-img img-sport" role="img" aria-label="Runner's shoes on a sunlit road"></div>
    <h3>Sporting Events</h3>
    <p>Lorem ipsum dolor sit amet, consectetuer adipiscing elit. Aenean commodo ligula</p>
    <div class="more"><svg width="18" height="8" viewBox="0 0 18 8"><path d="M1 5 Q5 0 9 4 Q13 8 17 2" stroke="#777" fill="none"/></svg>MORE<svg width="18" height="8" viewBox="0 0 18 8"><path d="M1 5 Q5 0 9 4 Q13 8 17 2" stroke="#777" fill="none"/></svg></div>
  </article>
  <article class="card">
    <div class="card-img img-estate" role="img" aria-label="Family together in a bright living room"></div>
    <h3>Real Estate Brochures</h3>
    <p>Lorem ipsum dolor sit amet, consectetuer adipiscing elit. Aenean commodo ligula</p>
    <div class="more"><svg width="18" height="8" viewBox="0 0 18 8"><path d="M1 5 Q5 0 9 4 Q13 8 17 2" stroke="#777" fill="none"/></svg>MORE<svg width="18" height="8" viewBox="0 0 18 8"><path d="M1 5 Q5 0 9 4 Q13 8 17 2" stroke="#777" fill="none"/></svg></div>
  </article>
  <article class="card">
    <div class="card-img img-camera" role="img" aria-label="Security camera on a white wall"></div>
    <h3>Surveillance</h3>
    <p>Lorem ipsum dolor sit amet, consectetuer adipiscing elit. Aenean commodo ligula</p>
    <div class="more"><svg width="18" height="8" viewBox="0 0 18 8"><path d="M1 5 Q5 0 9 4 Q13 8 17 2" stroke="#777" fill="none"/></svg>MORE<svg width="18" height="8" viewBox="0 0 18 8"><path d="M1 5 Q5 0 9 4 Q13 8 17 2" stroke="#777" fill="none"/></svg></div>
  </article>
</section>

<div class="footer-line"></div>

<section class="col about">
  <h2>About Us</h2>
  <p>CAVA certified company and CAVA endorsed pilot, with Full Public Liability Insurance. All operating licences are in place and are carried on the operator. All drones are maintained to full CAVA compliance standards</p>
  <p>CAVA certified company and CAVA endorsed pilot, with Full Public Liability Insurance. All operating licences are in place and are carried on the operator. All drones are maintained to full CAVA compliance standards</p>
</section>

<section class="col other">
  <h2>Other Services</h2>
  <ul>
    <li>Special Occasions, Children's Birthday Parties, Weddings</li>
    <li>Sporting events –4K &nbsp;Video of yourself participating in marathons etc</li>
    <li>Real Estate Brochures</li>
    <li>Construction project updates for remote stake holders</li>
    <li>Surveillance – Police, Local councilsworksafeetc</li>
    <li>Building/Roof Condition Inspections</li>
    <li>Lost pets</li>
    <li>Accident reconstructions</li>
    <li>Insurance assessing</li>
  </ul>
</section>

<section class="col location">
  <h2>Location</h2>
  <div class="loc-row">
    <svg width="13" height="11" viewBox="0 0 13 11"><path d="M6.5 0 L13 5.5 L11 5.5 L11 11 L8 11 L8 7.5 L5 7.5 L5 11 L2 11 L2 5.5 L0 5.5 Z" fill="#fff"/></svg>
    <span>Street Name, Pacific</span>
  </div>
  <div class="loc-row">
    <svg width="12" height="12" viewBox="0 0 12 12"><path d="M2.5 0.5 L4.5 3.5 L3.3 4.8 Q4.6 7.6 7.2 8.7 L8.5 7.5 L11.5 9.5 L10 11.5 Q3 10.5 0.5 2 Z" fill="#fff"/></svg>
    <span class="loc-phone">0400 555 210</span>
  </div>
  <h2 class="follow">Follow Us</h2>
  <div class="socials">
    <span style="background:#f07b1c"></span>
    <span style="background:#2b4a8b"></span>
    <span style="background:#2ea2e5"></span>
    <span style="background:#e25b9e"></span>
    <span style="background:#c8102e"></span>
    <span style="background:#2e7cc4"></span>
  </div>
</section>

<footer class="footbar"></footer>
<div class="copy">Copy Right © 2015 &nbsp;Skyward Rentals Pacific | All Rights Reserved</div>
<div class="privacy">Privacy Policy</div>
<div class="bottom-rule"></div>
</body>
</html>
```